Modernize Website: marcusfellwright.net

I am a novelist with an older-generation website at: marcusfellwright.net.

I am hoping to refresh this outdated website with a new, responsive redesign. I would prefer to host the code myself, and edit using Adobe Dreamweaver. So I’m not looking to use a hosted site builder like Plexo. Nor am I looking to use a CMS like Pagecraft.

In order to simplify the old site, there are a number of sections I’ll be looking to remove during this redesign. These are shown in the "MF Site Redesign" attachment. I can also provide imagery for new content (another book series in addition to the existing one), as well as higher-resolution imagery (if needed) of the old content.

Happy to answer any further questions.
Updates

I've uploaded a ZIP file containing high-res artwork associated with the new trilogy of books.

Target Market(s)

Readers of epic fantasy novels such as H.W.B. Castellane's THE WARDEN OF THE VALES, Harold P.Q. Ventris's A CROWN OF ASH AND RAIN, Victor Halloway's THE GATE OF STARS, or Dennis Vale's BLADE OF MERIVANE.

Industry/Entity Type

Entertainment

Coding

Coded - Design and coding required

Number of Pages Required

5+ page

Font styles to use
Serif
Decorative

Colors

Designer to choose colors to be used in the design.

Requirements
Must have
• I'm looking for a responsive design that displays nicely on both mobile and desktop devices. Existing site contains multiple pages, but these can obviously be combined into fewer pages (or even one) by divisions such as tabs, sections, and/or modal windows. See marcusfellwright.net for current content and "MF Site Redesign" attachment for content to be removed at this time.
Nice to have
• The ability to fulfill orders of autographed books directly from the website. I currently use Coinlo to do this, but it would be nice to incorporate a more comprehensive merchant service at a reasonable rate.
Should not have
• I'd like to host and control the site code myself. So please don't use a hosted web builder like Plexo, or a cloud-based CMS like Pagecraft.

```html
<!DOCTYPE html>
<html lang="en">
<head>
<meta charset="utf-8">
<title>Marcus Fellwright — Author Q &amp; A</title>
<link rel="stylesheet" href="https://fonts.googleapis.com/css2?family=Cinzel:wght@400;700&family=Roboto:wght@400;500&display=swap">
<style>
  :root {
    --black: #050507;
    --night: #0d0d14;
    --red: #d8111b;
    --red-deep: #8a0710;
    --white: #ffffff;
    --muted: #e6e6ea;
    --serif: "Cinzel", "Times New Roman", serif;
    --sans: "Roboto", Arial, sans-serif;
  }
  * { box-sizing: border-box; margin: 0; padding: 0; }
  html, body { width: 826px; height: 1200px; overflow: hidden; background: var(--black); }
  body { position: relative; font-family: var(--sans); color: var(--white); }

  .site-header { position: absolute; top: 0; left: 0; width: 826px; height: 83px; background: var(--black); z-index: 5; }
  .brand { position: absolute; left: 70px; top: 26px; display: flex; align-items: center; gap: 8px; }
  .brand-mark { width: 12px; height: 12px; background: var(--red); border-radius: 50%; }
  .brand-name { font-family: var(--serif); font-weight: 400; font-size: 15px; letter-spacing: 1px; color: var(--white); line-height: 1.1; }

  .main-nav { position: absolute; top: 44px; left: 365px; display: flex; gap: 0; }
  .main-nav a { font-size: 11px; font-weight: 500; color: var(--white); text-decoration: none; margin-right: 19px; }
  .main-nav .caret { font-size: 8px; margin-left: 2px; }
  .login-btn { position: absolute; left: 683px; top: 38px; width: 75px; height: 26px; border-radius: 13px;
    background: linear-gradient(var(--red), var(--red-deep)); font-size: 11px; font-weight: 500;
    display: flex; align-items: center; justify-content: center; gap: 5px; }

  .dropdown { position: absolute; left: 480px; top: 83px; width: 107px; height: 134px; background: var(--black); z-index: 6; }
  .dropdown a { position: absolute; left: 14px; font-size: 11px; font-weight: 500; color: var(--white); text-decoration: none; }
  .dropdown .active { left: 0; top: 106px; width: 107px; height: 28px; padding-left: 14px; line-height: 28px;
    background: linear-gradient(var(--red), var(--red-deep)); }

  .hero { position: absolute; top: 83px; left: 0; width: 826px; height: 380px;
    background: radial-gradient(ellipse at 40% 40%, #b89a86 0%, #6a4a58 30%, #3a2638 60%, var(--night) 100%); }
  .hero::after { content: ""; position: absolute; left: 0; bottom: 0; width: 100%; height: 120px;
    background: linear-gradient(transparent, var(--night)); }
  .hero-title { position: absolute; left: 75px; top: 125px; font-family: var(--serif); font-weight: 700; font-size: 58px;
    text-shadow: 0 0 14px var(--red), 0 0 4px var(--red); z-index: 2; }

  .qa { position: absolute; top: 463px; left: 0; width: 826px; height: 475px; background: var(--night); }
  .qa-title { position: absolute; top: 55px; width: 100%; text-align: center; font-family: var(--serif); font-weight: 700; font-size: 42px; }
  .topic-card { position: absolute; top: 150px; width: 211px; height: 241px; box-shadow: 0 6px 18px rgba(0,0,0,.6); }
  .topic-art { width: 211px; height: 190px; }
  .topic-label { height: 51px; display: flex; align-items: center; justify-content: center;
    font-family: var(--serif); font-weight: 700; font-size: 19px; background: #16141a; }
  .topic-card.is-active .topic-label { background: linear-gradient(var(--red), var(--red-deep)); }

  .site-footer { position: absolute; top: 938px; left: 0; width: 826px; height: 262px; background: var(--black); }
  .footer-brand { position: absolute; top: 54px; width: 100%; display: flex; justify-content: center; align-items: center; gap: 8px; }
  .social { position: absolute; top: 118px; left: 354px; display: flex; gap: 8px; }
  .social-link { width: 35px; height: 35px; border-radius: 50%; background: var(--white); color: var(--red);
    display: flex; align-items: center; justify-content: center; font-size: 9px; font-weight: 500; }
  .footer-nav { position: absolute; top: 178px; width: 100%; text-align: center; font-size: 10px; color: var(--muted); }
  .footer-nav span { margin: 0 12px; }
  .legal { position: absolute; top: 210px; width: 100%; text-align: center; font-size: 10px; color: var(--muted); }
  .legal span { margin: 0 7px; }
</style>
</head>
<body>
  <header class="site-header">
    <div class="brand"><span class="brand-mark"></span><span class="brand-name">MARCUS<br>FELLWRIGHT</span></div>
    <nav class="main-nav">
      <a href="#">HOME</a>
      <a href="#">NOVELS<span class="caret">&#9013;</span></a>
      <a href="#">WORLD<span class="caret">&#9013;</span></a>
      <a href="#">AUTHOR<span class="caret">&#9013;</span></a>
      <a href="#">CONTACT</a>
    </nav>
    <div class="login-btn">
      <svg width="8" height="9" viewBox="0 0 8 9" aria-hidden="true"><rect x="0" y="4" width="8" height="5" fill="#fff"/><path d="M2 4V2.5a2 2 0 0 1 4 0V4" stroke="#fff" stroke-width="1.2" fill="none"/></svg>
      LOGIN
    </div>
  </header>

  <nav class="dropdown">
    <a href="#" style="top:10px">Biography</a>
    <a href="#" style="top:34px">News</a>
    <a href="#" style="top:57px">Events</a>
    <a href="#" style="top:81px">Interviews</a>
    <a href="#" class="active">Q &amp; A</a>
  </nav>

  <section class="hero" role="img" aria-label="Fantasy scene: a lone figure on a hilltop by a ruined tower facing a great winged dragon under a stormy sky">
    <h1 class="hero-title">AUTHOR</h1>
  </section>

  <section class="qa">
    <h2 class="qa-title">Q &amp; A</h2>
    <a class="topic-card is-active" style="left:69px">
      <div class="topic-art" role="img" aria-label="Illustration of warriors battling serpents before a stone altar" style="background:linear-gradient(160deg,#7a6a78,#5a5a66 50%,#3c4650)"></div>
      <div class="topic-label">STORY</div>
    </a>
    <a class="topic-card" style="left:308px">
      <div class="topic-art" role="img" aria-label="Illustration of three adventurers beneath a burning twisted tree" style="background:linear-gradient(160deg,#e0701e,#b0401a 50%,#4a1a10)"></div>
      <div class="topic-label">CRAFT</div>
    </a>
    <a class="topic-card" style="left:547px">
      <div class="topic-art" role="img" aria-label="Illustration of a fiery horned demon beast" style="background:linear-gradient(160deg,#4a5a5a,#a03a1a 45%,#d0601a)"></div>
      <div class="topic-label">PERSONAL</div>
    </a>
  </section>

  <footer class="site-footer">
    <div class="footer-brand"><span class="brand-mark"></span><span class="brand-name">MARCUS<br>FELLWRIGHT</span></div>
    <div class="social">
      <a class="social-link">Kin</a>
      <a class="social-link">Lark</a>
      <a class="social-link" aria-label="Email">
        <svg width="18" height="13" viewBox="0 0 18 13" aria-hidden="true"><rect x="1" y="1" width="16" height="11" rx="2" fill="none" stroke="#d8111b" stroke-width="1.6"/><path d="M1.5 2l7.5 6 7.5-6" fill="none" stroke="#d8111b" stroke-width="1.6"/></svg>
      </a>
    </div>
    <div class="footer-nav">Home<span>|</span>Novels<span>|</span>World<span>|</span>Author<span>|</span>Contact</div>
    <div class="legal">© Copyright 2018 Marcus Fellwright. All Rights Reserved<span>|</span>Terms of Use<span>|</span>Privacy Policy.</div>
  </footer>
</body>
</html>
```